Commercial/Corporate Law Firm needs Website Design

Hi guys. I've started up a new law firm and would love your help designing an attractive website. I'll need both design and coding, and to make it easy for us to edit as necessary later, I think it should be built off a Wordpress.org structure.
FIRST IMPRESSIONS
It's very important that the first impression of the website really captures our prospective clients' attention and impresses them. Their first three seconds needs to be good.
I imagine the homepage may be short, with a menu bar and a compelling image, and with a tagline overlaid or underneath (eg. "It's about results.")
The image should be related to our practice areas: eg. IPOs, corporate transactions, or commercial negotiations.
I have previously suggested there could be a skyline image of Sydney or Adelaide. However, because we are based in Adelaide, I don't think Sydney is appropriate - and Adelaide is probably too boring to use.
HOMEPAGE
Being a new firm, we don't have many existing testimonials, and I will be the only lawyer to start with. So we need to focus on the nature of the services we will provide and how my experience can help them. We have an existing logo to use, and I would like the website colour scheme not to clash with that logo (dark blue and white).
After the initial image and tagline there should be a brief introduction to each of the main areas of work, eg. "We specialise in three main areas of practice:"
1. Corporate Transactions and Regulation
2. Business Law and Dispute Resolution
3. Migration Assistance
These should each have an appropriate photo and link to a separate page that briefly describes our services in that area.
Below that there should be a message from me with a photo. Finally, at the bottom, there should be a "Contact Us" section which shows a Google image of our address, contact details, and then our logo with colours inverted.
OTHER PAGES
While we will need some other pages, they should all be fairly simple. I think we will need one page to say "About Us", where I will put information about my experience. I think we will then need one page for each of the 3 areas listed above, which just needs an appropriate image and then text to describe the service. Finally, a "Contact Us" page which I imagine will be the same as the bottom of the homepage.
OTHER DETAILS
For now you can use details from my LinkedIn page to fill out any other text as necessary, or the photo.
Because the logo is square, I would prefer the design of the website also to be rectangular.
Looking forward to seeing your work! Thank you.
Marcus
Potential clients:
Businesses with legal issues or disputes
Companies wishing to list on the stock market

```html
<!DOCTYPE html>
<html lang="en">
<head>
<meta charset="utf-8">
<title>Calloway Legal</title>
<link href="https://fonts.googleapis.com/css2?family=Noto+Serif:ital,wght@0,400;0,700;1,400&family=Open+Sans:ital,wght@0,400;0,600;0,700;1,400&display=swap" rel="stylesheet">
<style>
:root{
  --navy:#1f2f5c;
  --navy-deep:#16234a;
  --ink:#222222;
  --text:#444444;
  --muted:#777777;
  --line:#d8d8d8;
  --paper:#ffffff;
  --band:#efefef;
  --footer:#161616;
  --footer-text:#cfcfcf;
}
*{box-sizing:border-box;margin:0;padding:0}
html,body{width:1200px;height:3586px;overflow:hidden;background:var(--paper)}
body{font-family:"Open Sans",Arial,sans-serif;color:var(--text);position:relative}
.abs{position:absolute}

/* header */
.site-header{position:absolute;left:0;top:0;width:1200px;height:105px;background:var(--paper);z-index:3}
.brand{position:absolute;left:92px;top:0;width:268px;height:180px;background:var(--paper);border-radius:0 0 134px 134px;z-index:4;text-align:center}
.brand-square{position:absolute;left:108px;top:14px;width:52px;height:52px;background:var(--navy)}
.brand-name{position:absolute;left:0;width:268px;top:86px;font-family:"Noto Serif",Georgia,serif;font-size:27px;letter-spacing:2px;color:var(--navy);line-height:1.15}
.brand-name span{display:block;font-size:15px;letter-spacing:8px}
.top-contact{position:absolute;right:132px;top:20px;display:flex;gap:34px;font-size:17px;color:var(--ink)}
.top-contact div{display:flex;align-items:center;gap:9px}
.main-nav{position:absolute;right:132px;top:64px;display:flex;gap:34px;font-family:"Noto Serif",Georgia,serif;font-size:15px;font-weight:700;color:var(--ink);letter-spacing:.5px}

/* hero */
.hero{position:absolute;left:0;top:105px;width:1200px;height:550px;background:linear-gradient(180deg,#3d4866 0%,#5d6a8a 35%,#b48a7a 62%,#2a3048 80%,#1c2238 100%)}
.hero-box{position:absolute;left:330px;top:200px;width:540px;height:168px;border:2px solid #fff;background:rgba(15,18,30,.55);text-align:center}
.hero-title{font-family:"Noto Serif",Georgia,serif;font-weight:700;font-size:52px;color:#fff;margin-top:26px;letter-spacing:1px}
.hero-btn{display:inline-block;margin-top:10px;border:2px solid #fff;color:#fff;font-size:15px;font-weight:600;padding:5px 12px}
.hero-arrow{position:absolute;top:280px;width:34px;height:34px;border-radius:50%;background:rgba(20,20,20,.7)}

/* section titles */
.section-title{position:absolute;left:0;width:1200px;text-align:center;font-family:"Noto Serif",Georgia,serif;font-weight:700;font-size:33px;color:var(--navy);letter-spacing:.5px}
.intro{position:absolute;left:200px;width:800px;text-align:center;font-size:13px;line-height:26px;color:var(--text)}

/* practice cards */
.card{position:absolute;top:940px;width:294px;height:380px;border:1px solid var(--line);background:#fff;text-align:center}
.card-img{height:175px;background:linear-gradient(135deg,#8896a8,#c9ced6)}
.card h3{font-family:"Noto Serif",Georgia,serif;font-size:17px;color:var(--ink);margin-top:28px;font-weight:400;letter-spacing:.5px}
.card p{font-size:12px;line-height:24px;margin:10px 14px 0}
.pill{display:inline-block;margin-top:14px;border:1.5px solid var(--ink);border-radius:14px;font-size:11px;font-weight:600;padding:4px 16px;color:var(--ink)}

/* about */
.about-band{position:absolute;left:0;top:1437px;width:1200px;height:618px;background:var(--band)}
.about-frame{position:absolute;left:505px;top:1605px;width:560px;height:350px;border:1.5px solid #6a6f7c}
.about-photo{position:absolute;left:130px;top:1535px;width:445px;height:370px;background:linear-gradient(135deg,#2a3450,#4b4a5c 55%,#a07a4e);box-shadow:0 6px 14px rgba(0,0,0,.25)}
.about-title{position:absolute;left:615px;top:1640px;font-family:"Noto Serif",Georgia,serif;font-weight:700;font-size:44px;color:var(--ink)}
.about-text{position:absolute;left:615px;top:1710px;width:420px;font-size:13px;line-height:24px}
.btn-navy{position:absolute;left:615px;top:1855px;background:var(--navy);color:#fff;font-size:13px;font-weight:600;padding:8px 16px;border-radius:3px}

/* testimonials */
.testimonials{position:absolute;left:0;top:2055px;width:1200px;height:395px;background:linear-gradient(180deg,var(--navy-deep),var(--navy))}
.testimonials .section-title{color:#fff;top:70px}
.quote{position:absolute;top:160px;width:440px}
.avatar{position:absolute;left:0;top:0;width:120px;height:120px;border-radius:50%;border:4px solid #fff;background:linear-gradient(160deg,#8a8f9c,#3b4258)}
.quote-text{position:absolute;left:135px;top:2px;width:310px;font-style:italic;font-size:13px;line-height:23px;color:#fff}
.stars{position:absolute;left:135px;top:110px;color:#fff;font-size:13px;letter-spacing:2px}
.quote-by{position:absolute;left:135px;top:140px;font-style:italic;font-size:12px;color:#dfe3ee;white-space:nowrap}
.quote-mark{position:absolute;left:35px;top:120px;font-family:"Noto Serif",Georgia,serif;font-size:60px;color:#fff;font-weight:700;line-height:1}

/* news */
.news{position:absolute;top:2625px;width:294px;height:428px;border:1px solid var(--line);border-radius:6px;background:#fff}
.news-img{height:183px;border-radius:6px 6px 0 0;background:linear-gradient(135deg,#6b6e78,#c8c4bd)}
.news-date{margin:18px 16px 0;font-size:13px;font-weight:700;color:var(--ink);display:flex;align-items:center;gap:8px}
.news h4{margin:12px 16px 0;font-family:"Noto Serif",Georgia,serif;font-weight:400;font-size:14.5px;line-height:22px;color:var(--navy);white-space:nowrap}
.news p{margin:10px 16px 0;font-size:11px;line-height:20px}
.news .tag{display:inline-block;margin:12px 16px 0;border:1.5px solid var(--ink);border-radius:3px;font-size:11px;font-weight:600;padding:3px 10px;color:var(--ink)}

/* footer */
.site-footer{position:absolute;left:0;top:3145px;width:1200px;height:441px;background:var(--footer);color:var(--footer-text)}
.foot-head{position:absolute;top:40px;font-family:"Noto Serif",Georgia,serif;font-weight:700;font-size:19px;color:#fff;letter-spacing:1px}
.foot-list{position:absolute;font-size:12.5px;line-height:29px}
.foot-list li{list-style:none;display:flex;gap:12px;align-items:flex-start}
.dot{display:inline-block;width:9px;height:9px;border-radius:50%;background:#fff;margin-top:10px}
.map{position:absolute;left:725px;top:100px;width:343px;height:205px;background:linear-gradient(135deg,#e6e4de,#d4dbe0)}
.foot-brand{position:absolute;left:435px;top:250px;width:150px;text-align:center}
.foot-brand .sq{width:40px;height:40px;background:#fff;margin:0 auto}
.foot-brand .nm{font-family:"Noto Serif",Georgia,serif;font-size:20px;color:#fff;letter-spacing:2px;margin-top:8px;line-height:1.2}
.foot-brand .nm span{display:block;font-size:11px;letter-spacing:6px}
.copyright{position:absolute;left:0;top:385px;width:1200px;border-top:1px solid #333;padding-top:18px;text-align:center;font-size:12px;color:#bbb}
.social{display:flex;gap:8px;margin-top:10px}
.social i{width:12px;height:12px;border-radius:50%;background:#fff;display:block}
</style>
</head>
<body>

<header class="site-header">
  <div class="top-contact">
    <div><svg width="24" height="24" viewBox="0 0 24 24"><circle cx="12" cy="12" r="10.5" fill="none" stroke="#222" stroke-width="1.5"/><path d="M8.5 7.5c.8-.8 1.5-.5 2 .3l.6 1.2c.3.6.1 1-.4 1.4.5 1.2 1.3 2 2.5 2.5.4-.5.8-.7 1.4-.4l1.2.6c.8.5 1.1 1.2.3 2-1.3 1.3-3.6.4-5.5-1.5S7.2 8.8 8.5 7.5z" fill="#222"/></svg>204-555-0148</div>
    <div><svg width="24" height="24" viewBox="0 0 24 24"><circle cx="12" cy="12" r="10.5" fill="none" stroke="#222" stroke-width="1.5"/><path d="M8.5 7.5c.8-.8 1.5-.5 2 .3l.6 1.2c.3.6.1 1-.4 1.4.5 1.2 1.3 2 2.5 2.5.4-.5.8-.7 1.4-.4l1.2.6c.8.5 1.1 1.2.3 2-1.3 1.3-3.6.4-5.5-1.5S7.2 8.8 8.5 7.5z" fill="#222"/></svg>info@callowaylegal.com</div>
  </div>
  <nav class="main-nav"><span>HOME</span><span>ABOUT US</span><span>PRACTICES</span><span>BLOG</span><span>CONTACT US</span></nav>
</header>
<div class="brand">
  <div class="brand-square"></div>
  <div class="brand-name">CALLOWAY<span>LEGAL</span></div>
</div>

<section class="hero" role="img" aria-label="City skyline over the harbour at dusk">
  <div class="hero-arrow" style="left:74px"><svg width="34" height="34" viewBox="0 0 34 34"><path d="M19 11l-6 6 6 6" fill="none" stroke="#fff" stroke-width="2.5"/></svg></div>
  <div class="hero-arrow" style="right:74px"><svg width="34" height="34" viewBox="0 0 34 34"><path d="M15 11l6 6-6 6" fill="none" stroke="#fff" stroke-width="2.5"/></svg></div>
  <div class="hero-box">
    <div class="hero-title">WE GET RESULTS</div>
    <div class="hero-btn">READ MORE</div>
  </div>
</section>

<h2 class="section-title" style="top:728px">OUR PRACTICES</h2>
<p class="intro" style="top:796px">Sed ut perspiciatis unde omnis iste natus error sit voluptatem accusantium doloremque laudantium, totam rem aperiam, eaque ipsa quae ab illo inventore veritatis et quasi architecto beatae vitae dicta sunt explicabo. Nemo enim ipsam voluptatem quia voluptas sit aspernatur aut odit aut fugit, sed quia consequuntur magni dolores eos qui ratione</p>

<article class="card" style="left:130px">
  <div class="card-img" role="img" aria-label="Business partners shaking hands in an office"></div>
  <h3>CORPORATE TRANSACTIONS</h3>
  <p>Sed ut perspiciatis unde omnis iste natus error sit voluptatem accusantium doloremque laudantium, totam rem aperiam, eaque ipsa quae</p>
  <span class="pill">READ MORE</span>
</article>
<article class="card" style="left:453px">
  <div class="card-img" role="img" aria-label="Lawyer meeting a client at a desk" style="background:linear-gradient(135deg,#7a6a58,#d3c8b8)"></div>
  <h3>BUSINESS LAW</h3>
  <p>Sed ut perspiciatis unde omnis iste natus error sit voluptatem accusantium doloremque laudantium, totam rem aperiam, eaque ipsa quae</p>
  <span class="pill">READ MORE</span>
</article>
<article class="card" style="left:774px">
  <div class="card-img" role="img" aria-label="Handshake in front of glass office towers" style="background:linear-gradient(135deg,#3f6fb0,#c9d8ea)"></div>
  <h3>MIGRATION ASSISTANCE</h3>
  <p>Sed ut perspiciatis unde omnis iste natus error sit voluptatem accusantium doloremque laudantium, totam rem aperiam, eaque ipsa quae</p>
  <span class="pill">READ MORE</span>
</article>

<section class="about-band"></section>
<div class="about-frame"></div>
<div class="about-photo" role="img" aria-label="Portrait of the principal lawyer with a night city skyline behind"></div>
<h2 class="about-title">About Calloway Legal</h2>
<p class="about-text">Sed ut perspiciatis unde omnis iste natus error sit voluptatem accusantium doloremque laudantium, totam rem aperiam, eaque ipsa quae ab illo inventore veritatis et quasi architecto beatae vitae dicta sunt explicabo. Nemo enim ipsam voluptatem quia voluptas sit aspernatur aut odit aut fugit, sed quia cntur magni dolores</p>
<span class="btn-navy">READ MORE</span>

<section class="testimonials">
  <h2 class="section-title">TESTIMONIALS</h2>
  <div class="quote" style="left:130px">
    <div class="avatar" role="img" aria-label="Client portrait"></div>
    <p class="quote-text">Sed ut perspiciatis unde omnis iste natus error sit voluptatem accusantium doloremque laudantium, totam rem aperiam, eaque ipsa quae ab illo inventore veritatis et quasi architecto beatae vitae</p>
    <div class="stars">★★★★★</div>
    <div class="quote-by">Sam Reyes - &nbsp;Calloway Legal</div>
    <div class="quote-mark">”</div>
  </div>
  <div class="quote" style="left:628px">
    <div class="avatar" role="img" aria-label="Client portrait"></div>
    <p class="quote-text">Sed ut perspiciatis unde omnis iste natus error sit voluptatem accusantium doloremque laudantium, totam rem aperiam, eaque ipsa quae ab illo inventore veritatis et quasi architecto beatae vitae</p>
    <div class="stars">★★★★★</div>
    <div class="quote-by">Sam Reyes - &nbsp;Calloway Legal</div>
    <div class="quote-mark">”</div>
  </div>
</section>

<h2 class="section-title" style="top:2522px">LATEST NEWS</h2>
<svg class="abs" style="left:82px;top:2800px" width="26" height="44" viewBox="0 0 26 44"><path d="M22 2L4 22l18 20" fill="none" stroke="#555" stroke-width="2"/></svg>
<svg class="abs" style="left:1092px;top:2800px" width="26" height="44" viewBox="0 0 26 44"><path d="M4 2l18 20L4 42" fill="none" stroke="#555" stroke-width="2"/></svg>

<article class="news" style="left:130px">
  <div class="news-img" role="img" aria-label="Signing documents at a desk"></div>
  <div class="news-date"><svg width="12" height="12" viewBox="0 0 12 12"><rect x="1" y="2" width="10" height="9" fill="none" stroke="#222" stroke-width="1.4"/><path d="M1 5h10M4 0v3M8 0v3" stroke="#222" stroke-width="1.4"/></svg>October 17, 2018</div>
  <h4>Quis autem vel eum iure reprehen<br>derit qui in ea voluptate</h4>
  <p>Sed ut perspiciatis unde omnis iste natus error sit voluptatem accusantium doloremque laudantium, totam rem aperiam, eaque ipsa quae</p>
  <span class="tag">READ MORE</span>
</article>
<article class="news" style="left:453px">
  <div class="news-img" role="img" aria-label="Team meeting around a boardroom table" style="background:linear-gradient(135deg,#4a3a2c,#a88a62)"></div>
  <div class="news-date"><svg width="12" height="12" viewBox="0 0 12 12"><rect x="1" y="2" width="10" height="9" fill="none" stroke="#222" stroke-width="1.4"/><path d="M1 5h10M4 0v3M8 0v3" stroke="#222" stroke-width="1.4"/></svg>October 17, 2018</div>
  <h4>Quis autem vel eum iure reprehen<br>derit qui in ea voluptate</h4>
  <p>Sed ut perspiciatis unde omnis iste natus error sit voluptatem accusantium doloremque laudantium, totam rem aperiam, eaque ipsa quae</p>
  <span class="tag">READ MORE</span>
</article>
<article class="news" style="left:774px">
  <div class="news-img" role="img" aria-label="Business person working on a laptop" style="background:linear-gradient(135deg,#1e2b44,#6a7a92)"></div>
  <div class="news-date"><svg width="12" height="12" viewBox="0 0 12 12"><rect x="1" y="2" width="10" height="9" fill="none" stroke="#222" stroke-width="1.4"/><path d="M1 5h10M4 0v3M8 0v3" stroke="#222" stroke-width="1.4"/></svg>October 17, 2018</div>
  <h4>Quis autem vel eum iure reprehen<br>derit qui in ea voluptate</h4>
  <p>Sed ut perspiciatis unde omnis iste natus error sit voluptatem accusantium doloremque laudantium, totam rem aperiam, eaque ipsa quae</p>
  <span class="tag">READ MORE</span>
</article>

<footer class="site-footer">
  <h3 class="foot-head" style="left:130px">CONTACT US</h3>
  <ul class="foot-list" style="left:130px;top:92px">
    <li><svg width="14" height="18" viewBox="0 0 14 18" style="margin-top:6px"><path d="M7 1a5.5 5.5 0 0 0-5.5 5.5C1.5 11 7 17 7 17s5.5-6 5.5-10.5A5.5 5.5 0 0 0 7 1z" fill="none" stroke="#ccc" stroke-width="1.4"/><circle cx="7" cy="6.5" r="2" fill="#ccc"/></svg><span style="line-height:20px;padding-top:4px">Calloway Legal<br>145 Harbour Street, Suite 410<br>Kingsford, SA, 5021</span></li>
    <li style="margin-top:6px"><svg width="16" height="16" viewBox="0 0 16 16" style="margin-top:6px"><path d="M3 2c1-1 2-.6 2.6.4l.8 1.5c.4.8.1 1.3-.5 1.8.7 1.6 1.7 2.6 3.3 3.3.5-.6 1-.9 1.8-.5l1.5.8c1 .6 1.4 1.6.4 2.6-1.7 1.7-4.7.5-7.2-2S1.3 3.7 3 2z" fill="#ccc"/></svg>Phone: (555) 201-3380</li>
    <li><svg width="16" height="16" viewBox="0 0 16 16" style="margin-top:6px"><rect x="1" y="5" width="14" height="9" fill="none" stroke="#ccc" stroke-width="1.3"/><rect x="4" y="1" width="8" height="4" fill="none" stroke="#ccc" stroke-width="1.3"/></svg>Fax: (555) 201-3391</li>
    <li><svg width="16" height="16" viewBox="0 0 16 16" style="margin-top:6px"><rect x="1" y="3" width="14" height="10" fill="none" stroke="#ccc" stroke-width="1.3"/><path d="M1 3l7 6 7-6" fill="none" stroke="#ccc" stroke-width="1.3"/></svg>Email : info@callowaylegal.com</li>
  </ul>
  <div class="abs" style="left:130px;top:290px;font-size:12px;font-weight:700;color:#fff">STAY CONNECTED WITH US
    <div class="social"><i></i><i></i><i></i></div>
  </div>

  <h3 class="foot-head" style="left:435px">PRACTICES</h3>
  <ul class="foot-list" style="left:435px;top:92px">
    <li><span class="dot"></span>Corporate Transactions</li>
    <li><span class="dot"></span>Regulation</li>
    <li><span class="dot"></span>Business Law</li>
    <li><span class="dot"></span>Dispute Resolution</li>
    <li><span class="dot"></span>Migration Assistance</li>
  </ul>
  <div class="foot-brand">
    <div class="sq"></div>
    <div class="nm">CALLOWAY<span>LEGAL</span></div>
  </div>

  <h3 class="foot-head" style="left:725px">MAP</h3>
  <div class="map" role="img" aria-label="Street map showing the office location"></div>

  <div class="copyright">(c) 2018 Calloway Legal | All Rights Reserved | Disclaimer</div>
</footer>

</body>
</html>
```